eBook Cover_H. Lindqvist-Borna
Schnell und zuverlässoig,Änderungswünsche wurden umgehend ausgeführt. Vielen Dank für das tolle Cover zu meinem ersten Buch!
Zielgruppe
freie Roman-Autorin (Erstlingswerk)
Zielgruppe: Lesende (Erwachsene), Frauen
Charakterisierung: magisch-realistischer Familienroman, spielt im Europa der Jetzt-Zeit
Aufgabenstellung
Im ersten Schritt geht es um ein Cover für ein eBook, das aber bei Bedarf als Book on Demand gedruckt werden soll. Es wird daher später Anforderung bzgl. Dicke / Umfang des gedruckten Buches und einer Rückseite geben. Das gewählte Design soll dann dahingehend überarbeitet und finale Druckdaten zur Verfügung gestellt werden. Dies soll von vornherein berücksichtigt werden und im Preis enthalten sein.
Titel: Regen über Glas, Monde im Moos
Autorinnenname: Henrike Lindqvist-Borna
des weiteren auf dem Cover: Roman

```html
<!DOCTYPE html>
<html lang="de">
<head>
<meta charset="utf-8">
<title>Regen über Glas, Monde im Moos – Henrike Lindqvist-Borna</title>
<link rel="stylesheet" href="https://fonts.googleapis.com/css2?family=Open+Sans:wght@400&family=Oswald:wght@700&display=swap">
<style>
  :root {
    --paper: #ffffff;
    --slate: #5b636a;
    --red-light: #f2401a;
    --red-mid: #d32a10;
    --red-deep: #8e1406;
    --white: #ffffff;
  }
  html, body {
    margin: 0;
    padding: 0;
    width: 841px;
    height: 1200px;
    overflow: hidden;
    background: var(--paper);
  }
  .cover {
    position: relative;
    width: 841px;
    height: 1200px;
    background: var(--paper);
    overflow: hidden;
  }
  .cover__author {
    position: absolute;
    top: 182px;
    left: 0;
    width: 100%;
    margin: 0;
    text-align: center;
    font-family: "Open Sans", Arial, sans-serif;
    font-weight: 400;
    font-size: 28px;
    letter-spacing: 0.01em;
    text-transform: uppercase;
    color: var(--slate);
    line-height: 1;
  }
  .cover__rule {
    position: absolute;
    top: 226px;
    left: 305px;
    width: 232px;
    height: 6px;
    background: var(--slate);
  }
  .cover__title {
    position: absolute;
    top: 288px;
    left: 0;
    width: 100%;
    margin: 0;
    text-align: center;
    font-family: "Oswald", "Arial Narrow", sans-serif;
    font-weight: 700;
    font-size: 78px;
    line-height: 82px;
    letter-spacing: 0.03em;
    text-transform: uppercase;
    color: var(--slate);
  }
  .cover__title span { display: block; }
  .cover__band {
    position: absolute;
    left: 0;
    top: 0;
    width: 841px;
    height: 1200px;
  }
  .cover__genre {
    position: absolute;
    top: 850px;
    left: 0;
    width: 100%;
    margin: 0;
    text-align: center;
    font-family: "Oswald", "Arial Narrow", sans-serif;
    font-weight: 700;
    font-size: 70px;
    line-height: 1;
    letter-spacing: 0.03em;
    color: var(--white);
  }
</style>
</head>
<body>
  <main class="cover">
    <svg class="cover__band" viewBox="0 0 841 1200" role="img" aria-label="Rotes Feld mit geschwungenen Wellenlinien und Kreismuster">
      <defs>
        <radialGradient id="band-glow" cx="0.45" cy="0.6" r="0.75">
          <stop offset="0" stop-color="var(--red-light)"/>
          <stop offset="0.55" stop-color="var(--red-mid)"/>
          <stop offset="1" stop-color="var(--red-deep)"/>
        </radialGradient>
      </defs>
      <polygon points="0,676 423,763 841,676 841,1200 0,1200" fill="url(#band-glow)"/>
    </svg>

    <p class="cover__author">Henrike Lindqvist-Borna</p>
    <div class="cover__rule"></div>
    <h1 class="cover__title">
      <span>Regen über Glas</span>
      <span>Monde im Moos</span>
    </h1>
    <p class="cover__genre">ROMAN</p>
  </main>
</body>
</html>
```